Business Card Design

Looking for business card designs for a new business. there will be two cards of the same design (both lots of information below in contact info). We would like the logo diagonally across the card with the information split above and below the logo similar to sketch. happy to look at similar alternatives
Please use same colours as in logo design

Industry/Entity Type

Business

Contact Information for Business Card

Dwight Halloran
mob - 0491 738 204
ph - 02 6148 3920
fax - 02 6148 3975
email - dwight@kestrelbeams.com.au
14 Larkmoor Road, Brellin NSW 2391

Colin Marchetti
mob - 0438 912 557
ph - 02 6148 3920
fax - 02 6148 3975
email - colin@kestrelbeams.com.au

```html
<!DOCTYPE html>
<html lang="en">
<head>
<meta charset="utf-8">
<title>Kestrel Beams – Business Cards</title>
<link href="https://fonts.googleapis.com/css2?family=Source+Sans+3:wght@400;600;700&display=swap" rel="stylesheet">
<style>
  :root {
    --teal: #148381;
    --ink: #111111;
    --paper: #ffffff;
    --backdrop: #ebe7e1;
    --edge: #3a3a3a;
  }
  * { box-sizing: border-box; margin: 0; padding: 0; }
  html, body {
    width: 1200px; height: 1190px; overflow: hidden;
    background: var(--backdrop);
    font-family: "Source Sans 3", Arial, sans-serif;
  }
  .canvas { position: relative; width: 1200px; height: 1190px; }

  .card {
    position: absolute;
    background: var(--paper);
    border: 1.5px solid var(--edge);
    border-radius: 30px;
    overflow: hidden;
  }
  .card--front { left: 216px; top: 26px; width: 943px; height: 537px; }
  .card--back  { left: 26px; top: 612px; width: 945px; height: 537px; }

  .wordmark {
    position: absolute;
    display: flex; align-items: center; gap: 18px;
    color: var(--ink);
    font-weight: 700;
    font-size: 80px;
    line-height: 1;
    letter-spacing: -0.5px;
    white-space: nowrap;
  }
  .wordmark__square { width: 46px; height: 46px; background: var(--ink); flex: none; }
  .card--front .wordmark { left: 190px; top: 112px; }
  .card--back .wordmark  { left: 170px; top: 210px; }

  .holder-name {
    position: absolute; left: 0; right: 0; top: 286px;
    text-align: center;
    color: var(--teal);
    font-weight: 700;
    font-size: 29px;
    line-height: 38px;
  }

  .sweep { position: absolute; left: 0; top: 0; width: 943px; height: 537px; }

  .contact {
    position: absolute; left: 0; right: 0; top: 395px;
    color: var(--paper);
    font-size: 22px;
    text-align: center;
    line-height: 45px;
  }
  .contact__row { display: flex; justify-content: center; align-items: center; gap: 6px; }
  .contact__row svg { width: 18px; height: 18px; fill: var(--paper); flex: none; }
  .contact__item { display: inline-flex; align-items: center; gap: 4px; }

  .website {
    position: absolute; left: 0; right: 0; top: 420px;
    text-align: center;
    font-size: 29px;
    letter-spacing: 2.5px;
    color: var(--ink);
  }
  .website strong { font-weight: 600; }
</style>
</head>
<body>
<div class="canvas">

  <section class="card card--front">
    <div class="wordmark"><span class="wordmark__square"></span>Kestrel Beams</div>
    <p class="holder-name">Colin Marchetti</p>

    <svg class="sweep" viewBox="0 0 943 537" aria-hidden="true">
      <path d="M0 456 Q471 268 943 456 L943 537 L0 537 Z" fill="var(--teal)"/>
      <path d="M0 440 Q471 260 943 440" fill="none" stroke="var(--ink)" stroke-width="6"/>
    </svg>

    <div class="contact">
      <div class="contact__row">
        <span class="contact__item">
          <svg viewBox="0 0 24 24"><path d="M6.6 10.8a15 15 0 0 0 6.6 6.6l2.2-2.2c.3-.3.7-.4 1-.2 1.1.4 2.3.6 3.6.6.6 0 1 .4 1 1V20c0 .6-.4 1-1 1A17 17 0 0 1 3 4c0-.6.4-1 1-1h3.5c.6 0 1 .4 1 1 0 1.3.2 2.5.6 3.6.1.3 0 .7-.2 1z"/></svg>
          02 6148 3920
        </span>
        <span class="contact__item">
          <svg viewBox="0 0 24 24"><path d="M8 1h8a2 2 0 0 1 2 2v18a2 2 0 0 1-2 2H8a2 2 0 0 1-2-2V3a2 2 0 0 1 2-2zm0 3v12h8V4zm4 14.5a1.3 1.3 0 1 0 0 2.6 1.3 1.3 0 0 0 0-2.6z"/></svg>
          0438 912 557
        </span>
        <span class="contact__item">
          <svg viewBox="0 0 24 24"><path d="M7 3h10v5H7zM4 9h16a2 2 0 0 1 2 2v7h-4v3H6v-3H2v-7a2 2 0 0 1 2-2zm4 7v3h8v-3z"/></svg>
          02 6148 3975
        </span>
      </div>
      <div class="contact__row">
        <span class="contact__item">
          <svg viewBox="0 0 24 24"><path d="M2 9l10-6 10 6v11H2zm2 1.2V18h16v-7.8l-8 5z"/></svg>
          colin@kestrelbeams.com.au
        </span>
      </div>
      <div class="contact__row">14 Larkmoor Road, Brellin NSW 2391</div>
    </div>
  </section>

  <section class="card card--back">
    <div class="wordmark"><span class="wordmark__square"></span>Kestrel Beams</div>
    <p class="website">www.<strong>kestrelbeams</strong>.com.au</p>
  </section>

</div>
</body>
</html>
```